Informational Site for Advanced Chemistry R&D

The company develops oxidation chemistry for air, water, fuel pollution controls. The site has been prototyped at www.velquaresearch.example. Take a look. Now, the task is to design it for eye-catching beauty with use of color, on-page scroll-driven color transition and parallax effects. Should capture the themes: high technology, wow it's beautiful, modern, uncluttered, clean urban environment.

Target Market(s)

China Environmentally Conscious Government and Industry,

Industry/Entity Type

It Company

Number of Pages Required

3 page

Font styles to use
Sans Serif

Requirements
Must have
• Parallax effects, desktop compatible, Rich, Modern, Simple, Graphic
Nice to have
• Mobile Phone Compatible
Should not have
• Flash, or anything that is slow to load or requires high bandwidth

```html
<!DOCTYPE html>
<html lang="en">
<head>
<meta charset="utf-8">
<title>Velqua – Advanced Oxidation Science</title>
<link rel="stylesheet" href="https://fonts.googleapis.com/css2?family=Raleway:wght@400;500;600;700&display=swap">
<style>
:root{
  --blue:#1f6fb5;
  --blue-dark:#17548f;
  --teal:#2bb3a8;
  --green:#27b07a;
  --green-light:#8fd14f;
  --ink:#333;
  --grey-bg:#e6e6e6;
  --footer:#383838;
  --white:#fff;
}
*{margin:0;padding:0;box-sizing:border-box}
html,body{width:1200px;height:2817px;overflow:hidden}
body{font-family:"Raleway",Arial,sans-serif;color:var(--ink);background:var(--white);position:relative}
.abs{position:absolute}

/* hero */
.hero{left:0;top:0;width:1200px;height:695px;background:linear-gradient(180deg,#cfe8f3 0%,#e8f4f8 40%,#f2f8ee 68%,#cfe8b4 100%);overflow:hidden}
.hero-waves{left:0;top:430px;width:1200px;height:265px}
.brand{left:100px;top:108px;display:flex;align-items:center;gap:12px}
.brand-dot{width:32px;height:32px;border-radius:50%;background:var(--teal)}
.brand-name{font-size:32px;font-weight:600;color:var(--blue)}
.nav{left:423px;top:0;width:777px;height:79px;background:linear-gradient(90deg,#2c88d0,#1a64ab);border-bottom-left-radius:40px;display:flex;align-items:center}
.nav a{flex:1;text-align:center;color:var(--white);text-decoration:none;font-size:15px;border-right:1px solid rgba(255,255,255,.25)}
.nav a:last-child{border-right:none}
.nav a.active{text-decoration:underline;text-underline-offset:8px}
.tag{left:100px;height:47px;color:var(--white);font-size:21px;line-height:47px;padding:0 18px}
.tag-1{top:263px;background:var(--blue)}
.tag-2{top:323px;background:var(--teal)}
.dots{left:100px;top:400px;display:flex;gap:18px}
.dots span{width:8px;height:8px;border-radius:50%;background:#3a4a5a}
.dots span.on{background:var(--blue)}
.globe{left:730px;top:100px;width:450px;height:450px;border-radius:50%;
  background:radial-gradient(circle,#f3f9e4 0%,#cbe79a 38%,#7dc04a 58%,#3e8f2f 70%,#2d6a27 76%,rgba(45,106,39,0) 80%)}

/* ideas */
.sec-title{width:1200px;text-align:center;font-size:30px;font-weight:700;color:var(--blue)}
.sec-title em{font-style:normal;color:var(--teal)}
.sec-rule{left:560px;width:80px;height:10px}
.sec-sub{width:1200px;text-align:center;font-size:13px;line-height:21px;color:#444}
.ideas-wave{left:0;top:960px;width:1200px;height:140px}
.idea{width:246px;height:304px;background:linear-gradient(180deg,#38b8b8,#1f75b8);border-radius:3px;box-shadow:0 4px 10px rgba(0,0,0,.2)}
.idea-ring{left:23px;top:22px;width:200px;height:200px;border-radius:50%;border:14px solid var(--white);border-right-color:transparent;border-left-color:transparent;transform:rotate(-20deg)}
.idea-img{left:48px;top:47px;width:150px;height:150px;border-radius:50%}
.idea-label{left:0;bottom:18px;width:246px;text-align:center;color:var(--white);font-size:19px;font-weight:600;letter-spacing:.5px}

/* oxidation band */
.ox{left:0;top:1230px;width:1200px;height:510px}
.ox-title{left:100px;top:1356px;font-size:28px;font-weight:500;color:var(--white)}
.ox-rule{left:100px;top:1402px;width:270px;height:2px;background:var(--white)}
.ox-text{left:100px;width:420px;font-size:13px;line-height:21px;color:#e6f0fb}
.ox-list{left:100px;top:1524px;list-style:none;font-size:13px;line-height:23px;color:#e6f0fb}
.ox-list li{display:flex;align-items:center;gap:10px}
.diagram{left:676px;top:1262px;width:320px;height:355px;border-radius:24px;
  background:radial-gradient(ellipse at 50% 50%,rgba(245,216,74,.85) 0%,rgba(190,220,110,.55) 35%,rgba(39,176,122,0) 72%)}

/* solutions */
.solutions{left:0;top:1720px;width:1200px;height:740px;background:var(--grey-bg)}
.sol{width:280px;height:416px;background:var(--blue);box-shadow:0 4px 10px rgba(0,0,0,.2);overflow:hidden}
.sol-img{left:0;top:0;width:280px;height:197px}
.sol-title{left:0;top:213px;width:280px;text-align:center;color:var(--white);font-size:19px;font-weight:500}
.sol-text{left:22px;top:252px;width:236px;text-align:center;color:#e2edf8;font-size:13px;line-height:21px}
.sol-btn{left:88px;top:332px;width:104px;height:30px;border-radius:15px;background:var(--teal);color:var(--white);font-size:12px;font-weight:600;text-align:center;line-height:30px}
.sol-foot{left:0;top:368px;width:280px;height:48px}

/* partners + footer */
.footer{left:0;top:2440px;width:1200px;height:377px;background:var(--footer)}
.partners{left:0;top:2360px;width:1200px;height:215px}
.partner-brand{left:175px;top:2500px;font-size:27px;font-weight:600;color:var(--white);display:flex;align-items:center;gap:10px}
.partner-brand i{width:26px;height:26px;border-radius:50%;background:var(--white)}
.badge{width:110px;height:110px;border-radius:50%}
.contact{left:103px;display:flex;align-items:center;gap:22px;color:#e8e8e8;font-size:14px;line-height:20px}
.contact svg{flex:none}
.foot-brand{left:450px;top:2632px;width:300px;display:flex;flex-direction:column;align-items:center;gap:12px}
.foot-brand i{width:60px;height:60px;border-radius:50%;background:var(--white)}
.foot-brand span{font-size:40px;font-weight:600;color:var(--white)}
.social{left:878px;top:2663px;display:flex;gap:20px}
.social span{width:34px;height:34px;border-radius:50%;border:2px solid #ddd}
.social span.on{background:var(--teal);border-color:var(--teal)}
.copy{left:855px;top:2736px;font-size:13px;color:#e8e8e8}
</style>
</head>
<body>

<section class="abs hero">
  <div class="abs globe" role="img" aria-label="Green planet ring with city skyline and a hand holding a seedling"></div>
  <svg class="abs hero-waves" viewBox="0 0 1200 265" preserveAspectRatio="none">
    <path d="M0 120 C300 60 600 90 900 110 S1150 60 1200 40 V265 H0Z" fill="#c8e69a" opacity=".7"/>
    <path d="M0 170 C350 110 700 150 950 150 S1150 110 1200 100 V265 H0Z" fill="#7cc96b" opacity=".8"/>
    <path d="M0 215 C400 170 800 200 1200 170 V265 H0Z" fill="#2fb57e"/>
  </svg>
</section>
<div class="abs brand"><i class="brand-dot"></i><span class="brand-name">Velqua</span></div>
<nav class="abs nav">
  <a class="active" href="#">Home</a><a href="#">Technology</a><a href="#">Products</a><a href="#">Contact</a>
</nav>
<div class="abs tag tag-1">Advanced Oxidation Science for</div>
<div class="abs tag tag-2">Environmental Pollution Management</div>
<div class="abs dots"><span></span><span></span><span class="on"></span></div>

<h2 class="abs sec-title" style="top:738px">New Ideas For A <em>Cleaner World</em></h2>
<svg class="abs sec-rule" style="top:782px" viewBox="0 0 80 10"><path d="M0 8 Q40 -2 80 8" stroke="var(--teal)" stroke-width="3" fill="none"/></svg>
<p class="abs sec-sub" style="top:801px">We use non-violent, creative confrontation to expose<br>global environmental problems</p>
<svg class="abs ideas-wave" viewBox="0 0 1200 140" preserveAspectRatio="none">
  <path d="M0 40 C300 140 700 60 900 40 S1150 20 1200 30 L1200 60 C1100 50 900 80 700 100 S250 120 0 60Z" fill="#9fdada" opacity=".7"/>
</svg>
<div class="abs idea" style="left:141px;top:876px">
  <div class="abs idea-ring"></div>
  <div class="abs idea-img" role="img" aria-label="Clear blue water surface" style="background:radial-gradient(circle at 40% 35%,#d6f1fa,#6fbfe4 55%,#2f86c2)"></div>
  <div class="abs idea-label">WATER</div>
</div>
<div class="abs idea" style="left:477px;top:876px">
  <div class="abs idea-ring"></div>
  <div class="abs idea-img" role="img" aria-label="Swirling grey air vortex" style="background:radial-gradient(circle,#e4e8ec,#8a939c 50%,#2e343b)"></div>
  <div class="abs idea-label">AIR</div>
</div>
<div class="abs idea" style="left:811px;top:876px">
  <div class="abs idea-ring"></div>
  <div class="abs idea-img" role="img" aria-label="Fuel pouring from a nozzle" style="background:radial-gradient(circle at 55% 60%,#e3b54a,#8c6a2a 50%,#26251f)"></div>
  <div class="abs idea-label">FUEL</div>
</div>

<section class="abs solutions"></section>
<svg class="abs ox" viewBox="0 0 1200 510" preserveAspectRatio="none">
  <defs>
    <linearGradient id="oxBlue" x1="0" y1="0" x2="0" y2="1"><stop offset="0" stop-color="#1b5fa0"/><stop offset="1" stop-color="#174f88"/></linearGradient>
  </defs>
  <path d="M0 10 C200 60 400 -10 593 30 V498 C400 470 200 510 0 490Z" fill="url(#oxBlue)"/>
  <path d="M593 30 C800 70 1000 -10 1200 20 V420 C1000 470 800 440 593 498Z" fill="var(--green)"/>
</svg>
<h2 class="abs ox-title">Advanced Oxidation</h2>
<div class="abs ox-rule"></div>
<p class="abs ox-text" style="top:1435px">Advanced Oxidation refers to a variety of techniques employing the Hydroxyl Radical, an energetic, highly reactive cousin of the water molecule:</p>
<ul class="abs ox-list">
  <li><svg width="12" height="12" viewBox="0 0 12 12"><path d="M1 6 L5 10 L11 1" stroke="#fff" stroke-width="2" fill="none"/></svg>To add oxygen to inorganic molecules</li>
  <li><svg width="12" height="12" viewBox="0 0 12 12"><path d="M1 6 L5 10 L11 1" stroke="#fff" stroke-width="2" fill="none"/></svg>To remove hydrogen from organic molecules</li>
</ul>
<p class="abs ox-text" style="top:1580px">These transformations convert important industrial contaminants into reactive forms that can be captured or that disintegrate into harmless end products.</p>
<div class="abs diagram" role="img" aria-label="Reaction map of the hydroxyl radical converting pollutant molecules"></div>

<h2 class="abs sec-title" style="top:1745px">Our <em>Solutions</em></h2>
<svg class="abs sec-rule" style="top:1789px" viewBox="0 0 80 10"><path d="M0 8 Q40 -2 80 8" stroke="var(--teal)" stroke-width="3" fill="none"/></svg>
<p class="abs sec-sub" style="top:1808px">We use non-violent, creative confrontation to expose<br>global environmental problems</p>

<article class="abs sol" style="left:100px;top:1884px">
  <div class="abs sol-img" role="img" aria-label="Refinery towers and pipes" style="background:linear-gradient(180deg,#b4bcc3,#6d757d 55%,#353a40)"></div>
  <h3 class="abs sol-title">Fuel Oil Desulfurization</h3>
  <p class="abs sol-text">Our proprietary low temperature and pressure advanced oxidation catalytic process reliably removes sulfur</p>
  <div class="abs sol-btn">LEARN MORE</div>
  <svg class="abs sol-foot" viewBox="0 0 280 48" preserveAspectRatio="none"><path d="M0 14 C90 46 190 46 280 6 V48 H0Z" fill="#fff"/></svg>
</article>
<article class="abs sol" style="left:460px;top:1884px">
  <div class="abs sol-img" role="img" aria-label="Technician handling chemical containers" style="background:linear-gradient(180deg,#b9c6cf,#6f8596 55%,#34506a)"></div>
  <h3 class="abs sol-title">Volatile Organic Compunds</h3>
  <p class="abs sol-text">Alkanes, alkenes, halogenated hydro carbons, aromatic hydrocarbons, esters, aldehydes, polycyclic</p>
  <div class="abs sol-btn">LEARN MORE</div>
  <svg class="abs sol-foot" viewBox="0 0 280 48" preserveAspectRatio="none"><path d="M0 14 C90 46 190 46 280 6 V48 H0Z" fill="#fff"/></svg>
</article>
<article class="abs sol" style="left:819px;top:1884px">
  <div class="abs sol-img" role="img" aria-label="Smokestacks releasing smoke" style="background:linear-gradient(180deg,#8591a0,#4a5563 55%,#1c2228)"></div>
  <h3 class="abs sol-title">Flue Gas Scrubbing</h3>
  <p class="abs sol-text">Desulfurization and denitrification using our proprietary flue gas advanced oxidation</p>
  <div class="abs sol-btn">LEARN MORE</div>
  <svg class="abs sol-foot" viewBox="0 0 280 48" preserveAspectRatio="none"><path d="M0 14 C90 46 190 46 280 6 V48 H0Z" fill="#fff"/></svg>
</article>

<footer class="abs footer"></footer>
<svg class="abs partners" viewBox="0 0 1200 215" preserveAspectRatio="none">
  <path d="M100 20 C400 70 800 -10 1100 30 V175 C800 215 400 150 100 190Z" fill="var(--green)"/>
</svg>
<div class="abs partner-brand"><i></i>Velqua</div>
<div class="abs badge" style="left:452px;top:2415px;background:#c53a3a"></div>
<div class="abs badge" style="left:706px;top:2386px;background:#2d5f9e"></div>
<div class="abs badge" style="left:923px;top:2396px;background:#e3a52a"></div>

<div class="abs contact" style="top:2648px">
  <svg width="28" height="28" viewBox="0 0 28 28"><circle cx="14" cy="14" r="13" fill="none" stroke="#ddd" stroke-width="1.5"/><path d="M14 7a4.5 4.5 0 0 0-4.5 4.5c0 3.5 4.5 9 4.5 9s4.5-5.5 4.5-9A4.5 4.5 0 0 0 14 7z" fill="#ddd"/><circle cx="14" cy="11.5" r="1.6" fill="#383838"/></svg>
  <span>Velqua Research Corp, Harbor Falls,<br>U.S.A.</span>
</div>
<div class="abs contact" style="top:2694px">
  <svg width="28" height="28" viewBox="0 0 28 28"><circle cx="14" cy="14" r="13" fill="none" stroke="#ddd" stroke-width="1.5"/><rect x="8" y="10" width="12" height="8" fill="#ddd"/><path d="M8 10 L14 15 L20 10" stroke="#383838" stroke-width="1.2" fill="none"/></svg>
  <span>info@velquaresearch.example</span>
</div>
<div class="abs contact" style="top:2740px">
  <svg width="28" height="28" viewBox="0 0 28 28"><circle cx="14" cy="14" r="13" fill="none" stroke="#ddd" stroke-width="1.5"/><path d="M10 8c1 0 2 2.5 2 3s-1 1-1 1.5 2 3.5 3.5 4c.5 0 1-1 1.5-1s3 1 3 2-1 2-2 2C12 19.5 8.5 14 8.5 10c0-1 .5-2 1.5-2z" fill="#ddd"/></svg>
  <span>+1 555 014 2290</span>
</div>
<div class="abs foot-brand"><i></i><span>Velqua</span></div>
<div class="abs social"><span></span><span class="on"></span><span></span><span></span></div>
<p class="abs copy">2016 @ Velqua. All Rights Reserved</p>

</body>
</html>
```